Marlowe Group needs a business card

I would like the card to be simple but modern and elegant.
I like black and white.
or black and gold.
we are a private finance lender and also are involved in property and property developments.

please look at the business card photos i provided i would like M.G only one one side and all the other details on the other side use fonts that tie in with my theme.

Industry/Entity Type

Finance

Contact Information for Business Card

Marlowe Group (M.G) Daniel Marlowe M: 0413586207 E: danmarl@inboxmail.test

Font styles to use
Other font styles liked:
• Use fonts that would reflect our business

Colors
000000
ffffff

Requirements
Must have
• one side of details
• other side has either M.G or Marlowe Group like in the photos provided

```html
<!DOCTYPE html>
<html lang="en">
<head>
<meta charset="UTF-8">
<title>Marlowe Group — Business Card</title>
<link rel="stylesheet" href="https://fonts.googleapis.com/css2?family=Cinzel:wght@400;700&family=Lato:wght@400&display=swap">
<style>
  :root {
    --backdrop: #808080;
    --card-black: #000000;
    --gold: #f5c21b;
    --gold-deep: #f2b90f;
    --gold-light: #fdf0b0;
    --white: #ffffff;
  }
  * { margin: 0; padding: 0; box-sizing: border-box; }
  html, body { width: 1200px; height: 900px; overflow: hidden; }
  body { background: var(--backdrop); position: relative; }

  .card {
    position: absolute;
    background: var(--card-black);
    border-radius: 12px;
    overflow: hidden;
    box-shadow: 2px 4px 6px rgba(0,0,0,0.35);
  }
  .card--details { left: 137px; top: 271px; width: 457px; height: 282px; }
  .card--brand   { left: 626px; top: 271px; width: 458px; height: 280px; }

  .gold-band {
    position: absolute; left: 0; width: 100%; height: 13px;
    background: linear-gradient(90deg, var(--gold-deep) 0%, var(--gold) 45%, var(--gold-light) 62%, var(--gold) 80%, var(--gold-deep) 100%);
  }
  .gold-band--top { top: 0; }
  .gold-band--bottom { bottom: 0; }

  .company-name {
    position: absolute; left: 0; width: 100%; top: 56px;
    text-align: center;
    font-family: "Cinzel", serif; font-weight: 400;
    font-size: 29px; color: var(--gold); letter-spacing: 0.5px;
  }
  .person-name {
    position: absolute; left: 0; width: 100%; top: 140px;
    text-align: center;
    font-family: "Cinzel", serif; font-weight: 700;
    font-size: 16.5px; color: var(--gold); letter-spacing: 0.3px;
  }
  .name-rule {
    position: absolute; left: 163px; top: 169px; width: 130px; height: 1px;
    background: linear-gradient(90deg, transparent, var(--gold) 50%, transparent);
  }
  .contact-list {
    position: absolute; left: 0; width: 100%; top: 179px;
    list-style: none; text-align: center;
    font-family: "Lato", sans-serif; font-size: 13px; line-height: 20px;
    color: var(--white);
  }
  .contact-label { color: var(--gold); }

  .brand-square {
    position: absolute; left: 180px; top: 80px; width: 100px; height: 100px;
    border: 3px solid var(--gold);
  }
  .brand-name {
    position: absolute; left: 0; width: 100%; top: 188px;
    text-align: center;
    font-family: "Cinzel", serif; font-weight: 400;
    font-size: 18.5px; color: var(--gold);
  }
</style>
</head>
<body>
  <section class="card card--details">
    <div class="gold-band gold-band--top"></div>
    <h1 class="company-name">Marlowe Group</h1>
    <h2 class="person-name">DANIEL MARLOWE</h2>
    <div class="name-rule"></div>
    <ul class="contact-list">
      <li><span class="contact-label">M:</span> 0413586207</li>
      <li><span class="contact-label">E:</span> danmarl@inboxmail.test</li>
    </ul>
    <div class="gold-band gold-band--bottom"></div>
  </section>

  <section class="card card--brand">
    <div class="brand-square"></div>
    <p class="brand-name">Marlowe Group</p>
  </section>
</body>
</html>
```